Classic and neutral book cover design

We are looking for a classic and neutral book cover design to be used as the template for a series of books to be published. We are hence looking for a template that will allow us to easily change the title name for all books in this series.
The use of very few colours (black and white is welcome) and few design elements is a big bonus. As a source of inspiration we would like to ask you to view the very simple and
If you think you have a cool idea that can add a twist to the formal classic look don't hesitate. Go for it !
Work will be done for a 30 year old Sweden based cultural non-profit called VĂ©ru (www.verufoundation.example). We work with the publishing and supporting of post-modern art and literature addressing contemporary topics but are also involved in assisting projects of cultural preservation.
Target Market(s)
The audience is expected to have some form of interest in culture but could range from hobbyist readers to tenure track scholars
Industry/Entity Type
Non-Profit
Requirements
Must have
- General:
- Classic and neutral feel
- Preferably very simple and few shapes
- usage of few colours (black and white is welcome)
Information to be displayed on the cover is:
- Author
- Title
- type of work e.g. play/novel (optional)
- publishing house (in this case "Veru Publishing")
Nice to have
- ideas to prevent it from become boring are of course welcome
Should not have
- - too many colours

```html
<!DOCTYPE html>
<html lang="en">
<head>
<meta charset="utf-8">
<title>Nice Title — Book Cover</title>
<link rel="stylesheet" href="https://fonts.googleapis.com/css2?family=Crimson+Text:ital,wght@0,400;1,400&display=swap">
<style>
  :root {
    --paper: #ffffff;
    --cover: #000000;
    --ink: #ffffff;
  }
  html, body {
    margin: 0;
    padding: 0;
    width: 952px;
    height: 1200px;
    overflow: hidden;
    background: var(--paper);
  }
  .canvas {
    position: relative;
    width: 952px;
    height: 1200px;
    background: var(--paper);
    font-family: "Crimson Text", "Times New Roman", serif;
  }
  .cover {
    position: absolute;
    left: 51px;
    top: 52px;
    width: 850px;
    height: 1103px;
    background: var(--cover);
    color: var(--ink);
  }
  .cover-line {
    position: absolute;
    left: 0;
    right: 0;
    margin: 0;
    text-align: center;
    line-height: 1;
    font-weight: 400;
    transform: translateY(-50%);
  }
  .publisher {
    top: 140px;
    font-size: 18px;
    font-style: italic;
    letter-spacing: 3px;
    text-transform: uppercase;
  }
  .title {
    top: 416px;
    font-size: 84px;
    letter-spacing: 17px;
    padding-left: 17px;
    text-transform: uppercase;
  }
  .work-type {
    top: 752px;
    font-size: 28px;
    font-style: italic;
  }
  .byline {
    top: 800px;
    font-size: 18px;
    font-style: italic;
  }
  .author {
    top: 841px;
    font-size: 31px;
    letter-spacing: 3.5px;
  }
</style>
</head>
<body>
  <div class="canvas">
    <section class="cover">
      <p class="cover-line publisher">Veru Publishing</p>
      <h1 class="cover-line title">Nice Title</h1>
      <p class="cover-line work-type">Novel</p>
      <p class="cover-line byline">by</p>
      <p class="cover-line author">Author Authorson</p>
    </section>
  </div>
</body>
</html>
```